FunBrixo Business Card

We need a business card design for our company. We sell construction-themed amusement rides for kids.

Contact Information for Business Card

Contact info on business card should include:
Carl Dunning
Co-Founder & COO
(833) 571-FUNBRIX
Carl@funbrixo-demo.com
www.funbrixo-demo.com

```html
<!DOCTYPE html>
<html lang="en">
<head>
<meta charset="utf-8">
<title>FunBrixo Business Card</title>
<link href="https://fonts.googleapis.com/css2?family=Roboto:wght@400;700&display=swap" rel="stylesheet">
<style>
  :root {
    --stage: #3b3b3c;
    --card: #2b292a;
    --orange: #f26f21;
    --white: #f2f2f2;
    --rule: #6d6b6c;
    --cyan: #29abe2;
    --magenta: #ec008c;
    --yellow: #f7a81b;
    --hardhat: rgba(214, 160, 40, 0.42);
    --shirt: rgba(170, 62, 44, 0.38);
    --vest: rgba(220, 110, 40, 0.34);
  }
  * { box-sizing: border-box; margin: 0; padding: 0; }
  html, body { width: 1200px; height: 1108px; overflow: hidden; }
  body {
    background: var(--stage);
    font-family: "Roboto", Arial, sans-serif;
    position: relative;
  }
  .card {
    position: absolute;
    top: 224px;
    width: 400px;
    height: 660px;
    background: var(--card);
    border-radius: 22px;
    overflow: hidden;
  }
  .card--front { left: 160px; }
  .card--back { left: 640px; }

  .brand {
    display: flex;
    align-items: center;
    justify-content: center;
    gap: 14px;
    color: var(--orange);
    font-weight: 700;
    font-size: 54px;
    letter-spacing: 0.5px;
  }
  .brand__dot {
    width: 26px; height: 26px;
    border-radius: 50%;
    background: var(--orange);
  }
  .card--front .brand { position: absolute; top: 150px; left: 0; right: 0; }

  .holder {
    position: absolute; top: 360px; left: 0; right: 0;
    text-align: center;
  }
  .holder__name {
    color: var(--orange);
    font-weight: 700;
    font-size: 26px;
    letter-spacing: 0.5px;
  }
  .holder__title {
    color: var(--white);
    font-size: 19px;
    margin-top: 4px;
  }
  .contact-icons {
    position: absolute; top: 440px; left: 40px; right: 40px;
    display: flex; align-items: center; gap: 10px;
  }
  .contact-icons__rule { flex: 1; height: 1px; background: var(--rule); }
  .icon {
    width: 32px; height: 32px; border-radius: 5px;
    display: flex; align-items: center; justify-content: center;
  }
  .icon--phone { background: var(--cyan); }
  .icon--mail { background: var(--magenta); }
  .icon--web { background: var(--yellow); }
  .icon svg { width: 20px; height: 20px; }

  .contact-list {
    position: absolute; top: 494px; left: 0; right: 0;
    list-style: none; text-align: center;
    color: var(--white); font-size: 19px; line-height: 30px;
  }

  .crew-art {
    position: absolute; left: 12px; right: 12px; height: 200px;
    border-radius: 14px;
    background:
      linear-gradient(180deg, var(--hardhat) 0%, transparent 30%, transparent 70%, rgba(43,41,42,0.6) 100%),
      linear-gradient(90deg, var(--shirt) 0%, var(--vest) 25%, var(--shirt) 50%, var(--vest) 75%, var(--shirt) 100%);
  }
  .crew-art--top { top: 12px; }
  .crew-art--bottom { bottom: 12px; }
  .card--back .brand { position: absolute; top: 300px; left: 0; right: 0; }
</style>
</head>
<body>
  <article class="card card--front">
    <div class="brand"><span class="brand__dot"></span>FunBrixo</div>

    <div class="holder">
      <p class="holder__name">CARL DUNNING</p>
      <p class="holder__title">Co-Founder &amp; COO</p>
    </div>

    <div class="contact-icons">
      <span class="contact-icons__rule"></span>
      <span class="icon icon--phone">
        <svg viewBox="0 0 20 20"><path d="M5 2h3l1.5 4-2 1.5a10 10 0 0 0 5 5l1.5-2 4 1.5v3a2 2 0 0 1-2 2A15 15 0 0 1 3 4a2 2 0 0 1 2-2z" fill="#1d1d1d"/></svg>
      </span>
      <span class="icon icon--mail">
        <svg viewBox="0 0 20 20"><rect x="2" y="5" width="16" height="11" fill="none" stroke="#1d1d1d" stroke-width="1.8"/><path d="M2 5l8 6 8-6" fill="none" stroke="#1d1d1d" stroke-width="1.8"/></svg>
      </span>
      <span class="icon icon--web">
        <svg viewBox="0 0 20 20"><circle cx="10" cy="10" r="7.5" fill="none" stroke="#1d1d1d" stroke-width="1.8"/><ellipse cx="10" cy="10" rx="3.2" ry="7.5" fill="none" stroke="#1d1d1d" stroke-width="1.5"/><path d="M2.5 10h15" stroke="#1d1d1d" stroke-width="1.5"/></svg>
      </span>
      <span class="contact-icons__rule"></span>
    </div>

    <ul class="contact-list">
      <li>(833) 571-FUNBRIX</li>
      <li>Carl@funbrixo-demo.com</li>
      <li>www.funbrixo-demo.com</li>
    </ul>
  </article>

  <article class="card card--back">
    <div class="crew-art crew-art--top" role="img" aria-label="Faded row of cartoon construction workers in yellow hard hats and safety vests shaking hands"></div>
    <div class="brand"><span class="brand__dot"></span>FunBrixo</div>
    <div class="crew-art crew-art--bottom" role="img" aria-label="Faded row of cartoon construction workers in yellow hard hats and safety vests shaking hands"></div>
  </article>
</body>
</html>
```